Velorin Health is a Direct primary office that needs a great flyer design

Velorin Health has been rebranded with a new logo and website and need new flyers to fit in with our new model and direction. Please refer to velorin-example.com for content. Attached is a possible layout.

```html
<!DOCTYPE html>
<html lang="en">
<head>
<meta charset="utf-8">
<title>Velorin Health – Direct Primary Care Flyer</title>
<link href="https://fonts.googleapis.com/css2?family=Poppins:wght@300;400;500;600;700;800&display=swap" rel="stylesheet">
<style>
:root{
  --blue:#4a5cf0;
  --green:#0b8a3c;
  --check:#0f8a3a;
  --ink:#222222;
  --grey:#5c5c5c;
  --soft:#777777;
  --white:#ffffff;
  --paper:#fafafa;
}
*{margin:0;padding:0;box-sizing:border-box}
html,body{width:842px;height:1200px;overflow:hidden;background:var(--white)}
body{position:relative;font-family:'Poppins',sans-serif;color:var(--ink)}
.sheet{position:absolute;left:44px;width:754px;background:var(--paper);box-shadow:0 6px 18px rgba(0,0,0,.22)}
.sheet-outside{top:42px;height:532px}
.sheet-inside{top:612px;height:532px}
.panel{position:absolute;top:0;height:100%;overflow:hidden}
.p1{left:0;width:246px}
.p2{left:246px;width:255px;background:var(--white)}
.p3{left:501px;width:253px;background:var(--paper)}
.bar{position:absolute;left:0;right:0;bottom:0;height:11px}
.bar.blue{background:var(--blue)}
.bar.green{background:var(--green)}

/* outside – cover */
.cover-photo{position:absolute;inset:0;background:linear-gradient(160deg,#4fb36a 0%,#2f9a86 40%,#3e86c8 75%,#4a6ee6 100%)}
.cover-headline{position:absolute;top:150px;left:0;width:246px;text-align:center;color:var(--white);font-weight:700;font-size:34px;line-height:37px;letter-spacing:.5px}
.brand{position:absolute;top:428px;left:0;width:246px;text-align:center;color:var(--white);font-size:23px;font-weight:400;letter-spacing:1px}
.brand-sub{position:absolute;top:458px;left:0;width:246px;text-align:center;color:var(--white);font-size:11.5px;font-weight:700;letter-spacing:.5px}

/* outside – contact */
.top-band{position:absolute;top:0;left:0;right:0;height:12px;background:var(--blue)}
.contact-photo{position:absolute;top:12px;left:0;right:0;height:360px;background:linear-gradient(180deg,#cfdbe3 0%,#e4ecf1 55%,#ffffff 100%)}
.contact{position:absolute;left:60px;top:0;list-style:none;font-size:11.5px;font-weight:500;color:var(--ink)}
.contact li{position:absolute;white-space:nowrap}
.contact svg{position:absolute;left:-19px;top:2px;width:11px;height:11px;fill:var(--check)}

/* outside – why */
.why-title{position:absolute;top:10px;left:8px;font-weight:800;font-size:34px;line-height:37.5px;color:var(--ink)}
.checks{position:absolute;left:23px;top:0;list-style:none;font-size:9.5px;line-height:12.8px;color:var(--ink);width:222px}
.checks li{position:absolute;left:0;width:222px;white-space:nowrap}
.tick{display:inline-block;width:10px;height:8px;margin-right:3px;vertical-align:-1px;fill:none;stroke:var(--check);stroke-width:2.6;stroke-linecap:round;stroke-linejoin:round}
.member-title{position:absolute;top:339px;left:8px;font-size:17.5px;font-weight:500;color:var(--grey);letter-spacing:.3px}

/* inside – benefits */
.benefits{position:absolute;inset:0;background:linear-gradient(180deg,#0b8a3c 0%,#14807a 45%,#2b66c8 100%)}
.benefits-title{position:absolute;top:10px;left:0;width:246px;text-align:center;color:var(--white);font-size:28px;font-weight:500;line-height:29.6px}
.benefits-body{position:absolute;top:323px;left:0;width:246px;text-align:center;color:var(--white);font-size:8.8px;line-height:11.4px;font-weight:500;white-space:nowrap}
.benefits-body p{margin-bottom:11.4px}

/* inside – about */
.about-photo{position:absolute;top:0;left:8px;right:0;height:239px;background:linear-gradient(160deg,#3a8fa8 0%,#3f78c0 55%,#2e8c8c 100%)}
.about-label{position:absolute;top:196px;right:22px;color:var(--white);font-size:20px;font-weight:500;letter-spacing:.5px}
.about-text{position:absolute;top:262px;left:0;width:255px;text-align:center;color:var(--soft);font-size:9px;line-height:14.1px;font-weight:300;white-space:nowrap;letter-spacing:-.1px}
.about-text p{margin-bottom:14.1px}

/* inside – faq */
.faq-block{position:absolute;left:0;width:253px;text-align:center;color:var(--soft);font-size:8.9px;font-weight:300;white-space:nowrap;letter-spacing:-.1px}
.faq-q{font-size:9.6px;font-weight:400;color:var(--grey);line-height:14px}
.faq-a1{line-height:12.9px}
.faq-a2{line-height:14.2px}
.faq-photo{position:absolute;left:0;right:0;top:437px;height:95px;background:linear-gradient(135deg,#2f5fc4 0%,#1d7f8e 55%,#0b8a3c 100%)}
.faq-label{position:absolute;right:12px;top:486px;color:var(--white);font-size:20px;font-weight:500}
</style>
</head>
<body>
<svg width="0" height="0" style="position:absolute">
  <defs>
    <symbol id="tick" viewBox="0 0 10 8"><path d="M1.3 4.2 L3.8 6.6 L8.7 1.3"/></symbol>
  </defs>
</svg>

<section class="sheet sheet-outside">
  <div class="panel p1">
    <div class="cover-photo" role="img" aria-label="Smiling patient at an eye exam chart, tinted green to blue"></div>
    <h1 class="cover-headline">IT IS<br>POSSIBLE TO<br>PAY LESS<br>AND<br>GET MORE.</h1>
    <div class="brand">VELORIN HEALTH</div>
    <div class="brand-sub">DIRECT PRIMARY CARE</div>
    <div class="bar blue"></div>
  </div>

  <div class="panel p2">
    <div class="top-band"></div>
    <div class="contact-photo" role="img" aria-label="Doctor in a white coat using a tablet with medical icons"></div>
    <ul class="contact">
      <li style="top:376px"><svg viewBox="0 0 24 24"><path d="M12 2a7 7 0 0 0-7 7c0 5 7 13 7 13s7-8 7-13a7 7 0 0 0-7-7zm0 9.5A2.5 2.5 0 1 1 12 6.5a2.5 2.5 0 0 1 0 5z"/></svg>1820 Maple Ridge Parkway</li>
      <li style="top:396px;left:-4px">Suite C Lakeview, GA 30099</li>
      <li style="top:423px;left:3px"><svg viewBox="0 0 24 24"><path d="M6.6 10.8a15.1 15.1 0 0 0 6.6 6.6l2.2-2.2a1 1 0 0 1 1-.25 11.4 11.4 0 0 0 3.6.57 1 1 0 0 1 1 1V20a1 1 0 0 1-1 1A17 17 0 0 1 3 4a1 1 0 0 1 1-1h3.5a1 1 0 0 1 1 1c0 1.25.2 2.45.57 3.57a1 1 0 0 1-.25 1z"/></svg>555-014-2278</li>
      <li style="top:455px;left:3px"><svg viewBox="0 0 24 24"><path d="M2 6l10 7 10-7V5H2zm0 2.4V19h20V8.4l-10 7z"/></svg>info@velorin-example.com</li>
      <li style="top:483px;left:3px"><svg viewBox="0 0 24 24"><path d="M12 2a10 10 0 1 0 0 20 10 10 0 0 0 0-20zm6.9 6h-2.9a15.6 15.6 0 0 0-1.4-3.6A8 8 0 0 1 18.9 8zM12 4c.8 1.2 1.5 2.5 1.9 4h-3.8c.4-1.5 1.1-2.8 1.9-4zM4.3 14a8 8 0 0 1 0-4h3.4a16.5 16.5 0 0 0 0 4zm.8 2h2.9c.3 1.3.8 2.5 1.4 3.6A8 8 0 0 1 5.1 16zM8 8H5.1a8 8 0 0 1 4.3-3.6C8.8 5.5 8.3 6.7 8 8zm4 12c-.8-1.2-1.5-2.5-1.9-4h3.8c-.4 1.5-1.1 2.8-1.9 4zm2.3-6H9.7a14.7 14.7 0 0 1 0-4h4.6a14.7 14.7 0 0 1 0 4zm.3 5.6c.6-1.1 1.1-2.3 1.4-3.6h2.9a8 8 0 0 1-4.3 3.6zm1.7-5.6a16.5 16.5 0 0 0 0-4h3.4a8 8 0 0 1 0 4z"/></svg>velorin-example.com</li>
    </ul>
    <div class="bar green"></div>
  </div>

  <div class="panel p3">
    <h2 class="why-title">WHY<br>CHOOSE<br>DIRECT<br>PRIMARY<br>CARE</h2>
    <ul class="checks">
      <li style="top:206px"><svg class="tick"><use href="#tick"/></svg>24/7 access to your doctor via telemedi-<br>cine, text, and phone consultations</li>
      <li style="top:244px"><svg class="tick"><use href="#tick"/></svg>Same day or next appointments</li>
      <li style="top:269px"><svg class="tick"><use href="#tick"/></svg>Low cost labs</li>
      <li style="top:294px"><svg class="tick"><use href="#tick"/></svg>Wellness Planning and health screenings<br>Unlimited appointments</li>
    </ul>
    <h3 class="member-title">Individual Member</h3>
    <ul class="checks">
      <li style="top:371px"><svg class="tick"><use href="#tick"/></svg>Age 21-45: $60/month</li>
      <li style="top:396px"><svg class="tick"><use href="#tick"/></svg>Age 46-64: $80/month</li>
      <li style="top:421px"><svg class="tick"><use href="#tick"/></svg>Age 65 and over $100/month</li>
      <li style="top:446px"><svg class="tick"><use href="#tick"/></svg>Age 17-20 with parent/guardian<br>membership: $25/month</li>
      <li style="top:485px"><svg class="tick"><use href="#tick"/></svg>Family plan discounts (must have 2<br>paid adults): 5%</li>
    </ul>
    <div class="bar blue"></div>
  </div>
</section>

<section class="sheet sheet-inside">
  <div class="panel p1">
    <div class="benefits"></div>
    <h2 class="benefits-title">DIRECT PRIMARY<br>CARE BENEFITS<br>PATIENTS BY<br>PROVIDING<br>SUBSTANTIAL<br>SAVINGS AND<br>A GREATER<br>DEGREE OF<br>ACCESS TO<br>YOUR DOCTOR</h2>
    <div class="benefits-body">
      <p>Chronic Illness</p>
      <p>We provide management of chronic illnesses<br>including, but not limited to diabetes, hypertension,<br>high cholesterol, heart disease, COPD,</p>
      <p>asthma, arthritis, gout, and thyroid disease.</p>
      <p>Acute Illness</p>
      <p>We treat a wide variety of common illnesses includ-<br>ing but not limited to respiratory infections, urinary<br>tract infections, kidney stones,</p>
      <p>Sexually transmitted infections, ear infections.</p>
    </div>
    <div class="bar blue"></div>
  </div>

  <div class="panel p2">
    <div class="about-photo" role="img" aria-label="Doctor listening to a patient's heartbeat, tinted blue"></div>
    <div class="about-label">ABOUT US</div>
    <div class="about-text">
      <p>Our mission is to provide patient-centered care that is<br>respectful, honest and compassionate.</p>
      <p>Our goal is to make a significant impact on the lives of<br>people in the surrounding communities through health<br>education, better care and disease prevention.</p>
      <p>We believe that health care should revolve around deci-<br>sions that patients make between themselves and their<br>doctor, not what the insurance-controlled model dictates<br>because of cost, time or convenience. As a Direct Primary<br>Care provider, we focus on you and your health without<br>the interference of outside interests. Our model allows<br>more time with you, 24/7 access to your provider, which<br>we believe is critical to developing relationships and<br>making appropriate decisions for wellness, medical care<br>and chronic care management.</p>
    </div>
    <div class="bar green"></div>
  </div>

  <div class="panel p3">
    <div class="faq-block faq-q" style="top:11px">What is direct primary care?</div>
    <div class="faq-block faq-a1" style="top:38px">Direct primary care is an affordable alternative<br>approach to health care and medical services. Instead<br>of dealing with costly co-pays and insurance claim<br>forms, and waiting to get reimbursed, DPC allows you to<br>pay a monthly, quarterly, or annual fee to the health<br>care provider of your choice. In return for this “member-<br>ship” or “retainer” fee, you have access to your medical<br>practitioner whenever you need them.</div>
    <div class="faq-block faq-q" style="top:156px">How is a direct primary care practice different?</div>
    <div class="faq-block faq-a2" style="top:185px">One of the biggest differences between DPC practices<br>and traditional practices is that in a DPC practice, you'll<br>have access to your health care provider at your con-<br>venience. Visits to the office for medical exams, routine<br>physicals, lab work, or other comprehensive health and<br>wellness services are unlimited, so you don't have to<br>worry about an expensive co-pay each time you make<br>an appointment. Your physician is there when you need<br>them most, so you can maintain good health, get<br>medical attention for an illness, or learn how to better<br>manage a chronic condition.</div>
    <div class="faq-block faq-a2" style="top:356px">Velorin Health offers DPC for its numerous advantages,<br>one of which is spending more time with your health<br>care provider at each visit. We believe in taking our time<br>with each individual, typically 30-45 minutes per visit,<br>so we can develop a therapeutic relationship to best</div>
    <div class="faq-photo" role="img" aria-label="Medical scan images on monitors, tinted blue and green"></div>
    <div class="faq-label">FAQ</div>
    <div class="bar blue"></div>
  </div>
</section>
</body>
</html>
```